Young, dynamic furniture company needs a new business card design

We require a new business card design for our modern furniture company which supplies furniture and appliances to the property and development market.
Oakridge Interiors has become one of the leading furniture & appliance suppliers to the property market withing London. With over 10 years experience, we have increased our business to supply not only private landlords and managing agents, but also property developers, housing associations and local councils.
We offer not only a complete range of furniture which includes beds, wardrobes, dining sets and sofas, but also a high quality, full delivery and assembly service to help you with all our furnishing needs.

Target Market(s)

Private landlords, estate agents, letting agents, property management companies

Industry/Entity Type

Business

Contact Information for Business Card

Name,
Title,
Address,
Mobile,
Telephone,
Fax, Website, email address

Font styles to use
Sans Serif

Colors
3176b5
0555a3
85abd2
cfdeed

Requirements
Must have
• All the above information for each of our staff, along with our logo

```html
<!DOCTYPE html>
<html lang="en">
<head>
<meta charset="utf-8">
<title>Oakridge Interiors — Business Card</title>
<link rel="stylesheet" href="https://fonts.googleapis.com/css2?family=Roboto:wght@400;500&display=swap">
<style>
  :root {
    --stage: #2e2f31;
    --brand-blue: #3176b5;
    --brand-navy: #0555a3;
    --brand-sky: #85abd2;
    --brand-mist: #cfdeed;
    --panel-dark: #2a2a2c;
    --ink: #1f1f21;
    --paper: #ffffff;
    --strip: #2d4f93;
  }
  * { box-sizing: border-box; margin: 0; padding: 0; }
  html, body {
    width: 1200px; height: 950px; overflow: hidden;
    background: var(--stage);
    font-family: "Roboto", Arial, sans-serif;
  }
  .canvas { position: relative; width: 1200px; height: 950px; }

  .card {
    position: absolute;
    width: 560px; height: 320px;
    box-shadow: 0 10px 30px rgba(0,0,0,.45);
    overflow: hidden;
  }

  /* Front */
  .card-front {
    left: 90px; top: 80px;
    background: var(--brand-blue);
    color: var(--paper);
    display: flex; flex-direction: column; align-items: center; justify-content: center;
    text-align: center;
  }
  .card-front .brand-name {
    font-size: 34px; font-weight: 500; letter-spacing: .5px; text-transform: uppercase;
  }
  .card-front .brand-tagline {
    margin-top: 6px; font-size: 12px; letter-spacing: 1px; text-transform: uppercase;
  }
  .card-front .front-web {
    margin-top: 42px; font-size: 15px; letter-spacing: 6px;
  }

  /* Back */
  .card-back {
    left: 550px; top: 540px;
    background: var(--paper);
  }
  .accent-strip {
    position: absolute; right: 0; top: 0;
    width: 16px; height: 220px;
    background: var(--strip);
  }
  .contact-panel {
    position: absolute; left: 0; bottom: 0;
    width: 240px; height: 240px;
    background: var(--panel-dark);
    color: var(--paper);
    padding: 22px 16px 0 22px;
    font-size: 13px; line-height: 1.35;
  }
  .person-name { color: var(--brand-blue); font-size: 15px; font-weight: 500; text-transform: uppercase; }
  .person-title { text-transform: uppercase; margin-bottom: 6px; }
  .address { margin-bottom: 8px; }
  .contact-list { list-style: none; }
  .contact-list li { display: flex; align-items: center; gap: 9px; height: 21px; }
  .contact-list svg { width: 12px; height: 12px; fill: var(--brand-sky); flex: none; }

  .brand-block {
    position: absolute; left: 280px; top: 110px; width: 250px;
    text-align: center; color: var(--ink);
  }
  .brand-block .brand-name {
    display: flex; align-items: center; justify-content: center; gap: 8px;
    font-size: 21px; font-weight: 500; text-transform: uppercase;
  }
  .brand-block .brand-mark {
    width: 12px; height: 12px; background: var(--brand-navy);
  }
  .brand-block .brand-tagline {
    margin-top: 5px; font-size: 10px; letter-spacing: .8px; text-transform: uppercase;
  }
</style>
</head>
<body>
<main class="canvas">

  <section class="card card-front" aria-label="Business card front">
    <div class="brand-name">Oakridge Interiors</div>
    <div class="brand-tagline">Trade Furniture Solutions</div>
    <div class="front-web">www.oakridge-int.com</div>
  </section>

  <section class="card card-back" aria-label="Business card back">
    <div class="accent-strip"></div>

    <div class="brand-block">
      <div class="brand-name"><span class="brand-mark"></span>Oakridge Interiors</div>
      <div class="brand-tagline">Trade Furniture Solutions</div>
    </div>

    <div class="contact-panel">
      <div class="person-name">Marcus Hale</div>
      <div class="person-title">President</div>
      <div class="address">2710 Alder Crescent<br>Brookvale, NY 11420</div>
      <ul class="contact-list">
        <li>
          <svg viewBox="0 0 24 24"><path d="M6.6 10.8a15 15 0 0 0 6.6 6.6l2.2-2.2c.3-.3.7-.4 1-.2 1.1.4 2.3.6 3.6.6.6 0 1 .4 1 1V20c0 .6-.4 1-1 1A17 17 0 0 1 3 4c0-.6.4-1 1-1h3.5c.6 0 1 .4 1 1 0 1.3.2 2.5.6 3.6.1.3 0 .7-.2 1z"/></svg>
          576 0142 7781
        </li>
        <li>
          <svg viewBox="0 0 24 24"><path d="M7 1h10a2 2 0 0 1 2 2v18a2 2 0 0 1-2 2H7a2 2 0 0 1-2-2V3a2 2 0 0 1 2-2zm0 3v14h10V4z"/></svg>
          868 0193 4460
        </li>
        <li>
          <svg viewBox="0 0 24 24"><path d="M6 2h9l3 3v4h2a2 2 0 0 1 2 2v8h-4v3H6v-3H2v-8a2 2 0 0 1 2-2h2zm2 2v5h8V6h-2V4zm0 12v4h8v-4z"/></svg>
          856 0175 2294
        </li>
        <li>
          <svg viewBox="0 0 24 24"><path d="M2 5h20v14H2zm2 2v.5l8 5 8-5V7zm0 3v7h16v-7l-8 5z"/></svg>
          marcus@oakridge-int.com
        </li>
        <li>
          <svg viewBox="0 0 24 24"><path d="M12 2a10 10 0 1 0 0 20 10 10 0 0 0 0-20zm6.9 6h-3a15 15 0 0 0-1.3-3.9A8 8 0 0 1 18.9 8zM12 4c.8 1.2 1.5 2.5 1.9 4h-3.8c.4-1.5 1.1-2.8 1.9-4zM4.3 14a8 8 0 0 1 0-4h3.4a16 16 0 0 0 0 4zm.8 2h3a15 15 0 0 0 1.3 3.9A8 8 0 0 1 5.1 16zm3-8h-3a8 8 0 0 1 4.3-3.9A15 15 0 0 0 8.1 8zM12 20c-.8-1.2-1.5-2.5-1.9-4h3.8c-.4 1.5-1.1 2.8-1.9 4zm2.3-6H9.7a14 14 0 0 1 0-4h4.6a14 14 0 0 1 0 4zm.3 5.9a15 15 0 0 0 1.3-3.9h3a8 8 0 0 1-4.3 3.9zm1.7-5.9a16 16 0 0 0 0-4h3.4a8 8 0 0 1 0 4z"/></svg>
          www.oakridge-int.com
        </li>
      </ul>
    </div>
  </section>

</main>
</body>
</html>
```